Business Card Design - VNT (company name)

Over 20 years of progressive technology design, migration and management experience that drives business objectives and streamlines operations. Continuously challenge conventions to meet and exceed business security, availability and functionality requirements. Maintain exceptional vendor relationships to ensure ongoing knowledge of emerging products and to secure preferred service agreements. Recruit and utilize top talent and foster a collegial environment that advances innovation and performance excellence. design logo using 3 arrows of different colors green, gold, blue

Industry/Entity Type

Progressive

Contact Information for Business Card

Martin K. Osgood
IT Strategist / Consultant

626.583.2907 MOsgood@vntosgood.example 4817 Brenning Court Pasadena, CA 91104

Colors
0255a3
f37122
fece3e

Requirements
Must have
• Note NEW EMAIL ADDRESS
• MOsgood@vntosgood.example
• NOTE NEW ORDER of the work I do.
• Infrastructure – Systems – Cybersecurity
Nice to have
• main color should be orange

```html
<!DOCTYPE html>
<html lang="en">
<head>
<meta charset="utf-8">
<title>VNT Business Card</title>
<link rel="stylesheet" href="https://fonts.googleapis.com/css2?family=Open+Sans:wght@400;600;700&display=swap">
<style>
  :root {
    --page-bg: #2b2a29;
    --card-top: #1c1d1f;
    --card-bottom: #0c0d0e;
    --brand-orange: #f37122;
    --brand-gold: #fece3e;
    --brand-blue: #0255a3;
    --name-gold: #f5b51c;
    --text-light: #e9e9e9;
    --text-muted: #c9c9c9;
  }
  * { box-sizing: border-box; margin: 0; padding: 0; }
  html, body { width: 1200px; height: 844px; overflow: hidden; }
  body {
    background: var(--page-bg);
    font-family: "Open Sans", Arial, sans-serif;
    position: relative;
  }
  .card {
    position: absolute;
    top: 268px;
    width: 540px;
    height: 309px;
    border-radius: 4px;
    background: linear-gradient(160deg, var(--card-top) 0%, var(--card-bottom) 100%);
    box-shadow: 0 14px 30px rgba(0,0,0,.45);
    overflow: hidden;
  }
  .card--front { left: 40px; }
  .card--back { left: 620px; }

  .identity { position: absolute; left: 30px; top: 42px; }
  .identity__name { color: var(--name-gold); font-size: 20px; font-weight: 600; line-height: 1.1; }
  .identity__title { color: var(--text-muted); font-size: 13px; margin-top: 3px; }

  .brand-mark {
    position: absolute;
    display: flex;
    align-items: center;
    gap: 10px;
  }
  .card--front .brand-mark { left: 322px; top: 88px; }
  .card--back .brand-mark { left: 50%; top: 92px; transform: translateX(-50%); }
  .brand-mark__dot {
    width: 22px; height: 22px; border-radius: 50%;
    background: var(--brand-orange);
  }
  .brand-mark__name {
    color: var(--brand-orange);
    font-size: 46px;
    font-weight: 700;
    letter-spacing: 2px;
    line-height: 1;
  }

  .address {
    position: absolute; left: 30px; top: 178px;
    color: var(--text-light); font-size: 15px; line-height: 1.2;
  }
  .contacts { position: absolute; left: 30px; top: 232px; list-style: none; }
  .contacts__item {
    display: flex; align-items: center; gap: 10px;
    color: var(--text-light); font-size: 15px; height: 24px;
  }
  .contacts__icon {
    width: 18px; height: 18px; border-radius: 3px;
    background: var(--brand-orange);
    display: flex; align-items: center; justify-content: center;
    flex: none;
  }

  .services {
    position: absolute; left: 0; right: 0; top: 228px;
    display: flex; justify-content: center; gap: 8px;
    list-style: none;
    color: var(--text-light);
    font-size: 11.5px; font-weight: 600;
  }
  .services__item + .services__item::before {
    content: "|";
    margin-right: 8px;
  }
</style>
</head>
<body>
  <section class="card card--front" aria-label="Business card front">
    <div class="identity">
      <p class="identity__name">Martin K. Osgood</p>
      <p class="identity__title">IT Strategist / Consultant</p>
    </div>

    <div class="brand-mark">
      <span class="brand-mark__dot"></span>
      <span class="brand-mark__name">VNT</span>
    </div>

    <p class="address">4817 Brenning Court<br>Pasadena, CA 91104</p>

    <ul class="contacts">
      <li class="contacts__item">
        <span class="contacts__icon">
          <svg width="10" height="12" viewBox="0 0 10 12"><rect x="1.5" y="0.8" width="7" height="10.4" rx="1.2" fill="none" stroke="#fff" stroke-width="1.3"/><circle cx="5" cy="9.3" r=".8" fill="#fff"/></svg>
        </span>
        626.583.2907
      </li>
      <li class="contacts__item">
        <span class="contacts__icon">
          <svg width="12" height="9" viewBox="0 0 12 9"><rect x=".7" y=".7" width="10.6" height="7.6" rx="1" fill="none" stroke="#fff" stroke-width="1.2"/><path d="M1 1.2 L6 5 L11 1.2" fill="none" stroke="#fff" stroke-width="1.2"/></svg>
        </span>
        MOsgood@vntosgood.example
      </li>
    </ul>
  </section>

  <section class="card card--back" aria-label="Business card back">
    <div class="brand-mark">
      <span class="brand-mark__dot"></span>
      <span class="brand-mark__name">VNT</span>
    </div>
    <ul class="services">
      <li class="services__item">IT Strategist</li>
      <li class="services__item">Consultant</li>
      <li class="services__item">Infrastructure</li>
      <li class="services__item">Systems</li>
      <li class="services__item">Cybersecurity</li>
    </ul>
  </section>
</body>
</html>
```